Harborview Estates Business Card for Apartment Buildings

Create business cards for resident managers who run apartment buildings. The audience is the public who are searching for apartment rentals, and current residents who live at the apartment building. Key design element will be incorporating the company logo, however, the logo cannot dominate. The building name and manager name are more important than the logo. Current business card design leaves little room for copy, so we may need to reduce the size on the current card to allow for more space for copy.

Target Market(s)

Adults 18-65 years of age, who are looking for an apartment rental, plus current residents who live at our apartment buildings.

Industry/Entity Type

Property Management

Contact Information for Business Card

A major design element will be use of the company logo. Important property and manager contact information must be part of the design. The size of the logo will need to be reduced to make room for building and manager contact copy.

Font styles to use
Sans Serif

Colors
3176b5
000000
959595
ffffff

Requirements
Must have
• 1) Incorporate the company logo.
• 2) Use the company colors (dark blue, black/grey, over white).
• 3) FEATURE THE BUILDING NAME
• 4) FEATURE THE MANAGER NAME
• 5) The company name is less important than BUILDING and MANAGER
• 6) Manager contact information
• **SEE ATTACHED CREATIVE BRIEF**
Nice to have
• 1) Back of card logo watermark
• 2) Ability to write notes on back of carfd
Should not have
• Avoid letting the company logo dominate the card, the building name and manager are more important than the company logo.

```html
<!DOCTYPE html>
<html lang="en">
<head>
<meta charset="utf-8">
<title>Harborview Estates – Business Card</title>
<link rel="stylesheet" href="https://fonts.googleapis.com/css2?family=Lato:wght@400;700&display=swap">
<style>
  :root {
    --brand-blue: #1769a8;
    --ink: #333333;
    --grey: #4a4a4c;
    --white: #ffffff;
    --stage: #1e1e1f;
  }
  * { margin: 0; padding: 0; box-sizing: border-box; }
  html, body { width: 1200px; height: 897px; overflow: hidden; }
  body {
    background: var(--stage);
    font-family: "Lato", sans-serif;
    position: relative;
  }
  .card {
    position: absolute;
    left: 303px;
    width: 595px;
    height: 338px;
    border-radius: 19px;
    overflow: hidden;
  }
  .card-front { top: 92px; background: var(--white); }
  .card-back { top: 469px; background: var(--brand-blue); }

  .brand-ring { position: absolute; left: 0; top: 0; }

  .company-name {
    position: absolute;
    left: 334px;
    top: 38px;
    color: var(--brand-blue);
    font-weight: 700;
    font-size: 21px;
    line-height: 24px;
    letter-spacing: 0.5px;
  }
  .manager-name {
    position: absolute;
    left: 334px;
    top: 100px;
    color: var(--brand-blue);
    font-size: 21px;
    font-weight: 400;
    line-height: 24px;
  }
  .manager-title {
    position: absolute;
    left: 334px;
    top: 122px;
    color: var(--ink);
    font-size: 14px;
  }
  .building-name {
    position: absolute;
    left: 334px;
    top: 148px;
    color: var(--brand-blue);
    font-size: 17px;
  }
  .building-address {
    position: absolute;
    left: 334px;
    top: 166px;
    color: var(--ink);
    font-size: 14px;
    line-height: 17px;
    font-style: normal;
  }
  .contact-list {
    position: absolute;
    left: 334px;
    top: 210px;
    list-style: none;
    color: var(--ink);
    font-size: 14px;
  }
  .contact-list li {
    display: flex;
    align-items: center;
    height: 19px;
  }
  .contact-list svg {
    width: 10px;
    height: 10px;
    margin-right: 12px;
    flex: none;
  }

  .back-watermark { position: absolute; left: 0; top: 0; }
  .back-name {
    position: absolute;
    left: 0;
    right: 0;
    top: 150px;
    text-align: center;
    color: var(--white);
    font-weight: 700;
    font-size: 40px;
    line-height: 46px;
    letter-spacing: 1px;
  }
  .back-web {
    position: absolute;
    left: 0;
    right: 0;
    top: 290px;
    text-align: center;
    color: var(--white);
    font-size: 15px;
    letter-spacing: 0.5px;
  }
</style>
</head>
<body>

<section class="card card-front">
  <svg class="brand-ring" width="300" height="338" viewBox="0 0 300 338" aria-hidden="true">
    <circle cx="153" cy="172" r="132" fill="none" stroke="var(--grey)" stroke-width="8"/>
  </svg>

  <div class="company-name">HARBORVIEW<br>ESTATES LLC</div>

  <h1 class="manager-name">Marisol Vantreese</h1>
  <p class="manager-title">Resident Manager</p>

  <h2 class="building-name">Cedar Court Apartments</h2>
  <address class="building-address">2845 Linden Avenue<br>Bayside, CA 90210</address>

  <ul class="contact-list">
    <li>
      <svg viewBox="0 0 10 10"><path d="M2 0.5 L3.6 0.5 L4.2 3 L3 3.8 C3.6 5.3 4.7 6.4 6.2 7 L7 5.8 L9.5 6.4 L9.5 8 C9.5 9 8.7 9.5 8 9.5 C4 9.2 0.8 6 0.5 2 C0.5 1.3 1 0.5 2 0.5 Z" fill="var(--brand-blue)"/></svg>
      555-210-4471
    </li>
    <li>
      <svg viewBox="0 0 10 10"><rect x="2.5" y="0.5" width="5" height="3" fill="var(--brand-blue)"/><rect x="0.5" y="3.5" width="9" height="4" rx="1" fill="var(--brand-blue)"/><rect x="2.5" y="6.5" width="5" height="3" fill="var(--brand-blue)"/></svg>
      555-210-4472
    </li>
    <li>
      <svg viewBox="0 0 10 10"><rect x="2.2" y="0.5" width="5.6" height="9" rx="1" fill="none" stroke="var(--brand-blue)" stroke-width="1.4"/><circle cx="5" cy="7.6" r="0.7" fill="var(--brand-blue)"/></svg>
      555-384-9106
    </li>
    <li>
      <svg viewBox="0 0 10 10"><rect x="0.7" y="2" width="8.6" height="6" fill="none" stroke="var(--brand-blue)" stroke-width="1.2"/><path d="M0.7 2 L5 5.5 L9.3 2" fill="none" stroke="var(--brand-blue)" stroke-width="1.2"/></svg>
      marisol@harborviewest.com
    </li>
    <li>
      <svg viewBox="0 0 10 10"><circle cx="5" cy="5" r="4.3" fill="none" stroke="var(--brand-blue)" stroke-width="1"/><ellipse cx="5" cy="5" rx="1.9" ry="4.3" fill="none" stroke="var(--brand-blue)" stroke-width="0.9"/><path d="M0.7 5 H9.3" stroke="var(--brand-blue)" stroke-width="0.9"/></svg>
      www.harborviewest.com
    </li>
  </ul>
</section>

<section class="card card-back">
  <svg class="back-watermark" width="595" height="338" viewBox="0 0 595 338" aria-hidden="true">
    <circle cx="301" cy="163" r="148" fill="var(--white)" fill-opacity="0.07"/>
  </svg>
  <div class="back-name">HARBORVIEW<br>ESTATES LLC</div>
  <p class="back-web">www.harborviewest.com</p>
</section>

</body>
</html>
```